Marwick Partners Exit Plan business consultant web site

This website is for a consulting business that helps other businesses with exit plans. Essentially, assists them with the sale of their business. This website should be very professional, almost with a wall street look. I would like a very attractive image on the homepage. Perhaps something that denotes success. Perhaps a picture of palm trees and a beach? I will leave it to you for interpretation.

Across the screen I would like the words "Does your business have an exit plan?"

Below that it should read the following:
Let us help you with a completely impartial, no obligation assessment (button with link to the contact page)

Also, please use logo in a prominent place on the website so it's easily seen.

Target Market(s)

Males 40+

Coding

Coded - Design and coding required

Number of Pages Required

5+ page

Colors

Designer to choose colors to be used in the design.

Requirements
Must have
• The tabs for the homepage on the top should be:
• 1. About us
• 2. Services
• 3. Industries
• 4. Our success
• 5. Contact
Nice to have
• Clean, professional image.
• Please put FB, TW, Linked In - logos at bottom.
• Here are two examples of a website to give you an idea:
• https://notes.quelvarocapital.example/library/why-every-business-owner-should-have-an-exit-plan
Should not have
• nothing whimsical or cartoon like

```html
<!DOCTYPE html>
<html lang="en">
<head>
<meta charset="utf-8">
<title>Marwick Partners — Exit Planning Consultants</title>
<link href="https://fonts.googleapis.com/css2?family=Playfair+Display:wght@400;700&family=Roboto:wght@400;500&display=swap" rel="stylesheet">
<style>
:root{
  --blue:#1f7fd1;
  --blue-dark:#1566b0;
  --ink:#1d1d1d;
  --text:#555;
  --muted:#777;
  --pale:#eef6fd;
  --line:#d9e3ec;
  --white:#fff;
}
*{box-sizing:border-box;margin:0;padding:0}
html,body{width:1200px;height:4010px;overflow:hidden}
body{position:relative;background:var(--white);font-family:'Roboto',sans-serif;color:var(--text)}
.abs{position:absolute}
.serif{font-family:'Playfair Display',serif;color:var(--ink);font-weight:700}
.center{text-align:center}

/* header */
.topbar{left:0;top:0;width:1200px;height:4px;background:var(--blue)}
.header{left:0;top:4px;width:1200px;height:96px;background:var(--white)}
.brand{left:108px;top:4px;width:220px;height:132px;background:var(--white);clip-path:polygon(0 0,100% 0,88% 100%,12% 100%);z-index:3;display:flex;flex-direction:column;align-items:center;justify-content:center;gap:10px}
.brand-mark{width:46px;height:46px;background:var(--ink)}
.brand-name{font-family:'Roboto',sans-serif;font-size:17px;color:var(--ink);letter-spacing:1px;font-weight:400}
.nav{top:42px;font-size:15px;color:var(--ink);font-weight:500}
.nav.active{color:var(--blue)}
.nav-mark{left:505px;top:20px;width:14px;height:14px;background:var(--ink)}

/* hero */
.hero{left:0;top:100px;width:1200px;height:546px;background:linear-gradient(180deg,#3d6fa6 0%,#6d8fb6 32%,#2d3d52 58%,#1b2330 100%)}
.hero-band{left:260px;top:246px;width:680px;height:170px;background:rgba(120,120,120,.45)}
.hero-title{left:0;top:262px;width:1200px;font-size:44px;line-height:52px;color:var(--white)}
.hero-sub{left:0;top:398px;width:1200px;font-size:17px;color:var(--white);font-weight:500}
.arrow{width:40px;height:40px;border:2px solid var(--white);border-radius:50%}
.btn-frame{border:2px solid var(--blue);padding:4px}
.btn{display:flex;align-items:center;justify-content:center;gap:8px;background:var(--blue);color:var(--white);font-weight:500;width:100%;height:100%;font-size:15px}

/* about */
.eyebrow{left:0;top:754px;width:1200px;font-size:20px;color:var(--ink)}
.h2{left:0;width:1200px;font-size:34px}
.body-p{font-size:15px;line-height:28px;color:var(--text)}

/* services */
.services{left:0;top:1153px;width:1200px;height:445px;background:linear-gradient(135deg,#c9d8e6,#e9f0f6 45%,#d3dfea)}
.card{top:1295px;width:229px;height:230px;background:var(--white);box-shadow:0 2px 8px rgba(0,0,0,.08);overflow:hidden}
.card-icon{position:absolute;left:62px;top:-36px;width:104px;height:104px;border-radius:50%;background:var(--blue)}
.card-icon svg{position:absolute;left:32px;top:44px}
.card h3{position:absolute;top:90px;width:100%;text-align:center;font-size:19px;font-weight:400;color:var(--ink)}
.card p{position:absolute;top:126px;left:14px;right:14px;text-align:center;font-size:14px;line-height:24px;color:var(--muted)}
.side-arrow{width:42px;height:42px;border:2px solid var(--blue);border-radius:50%;top:1390px}

/* feature */
.feature-h{left:110px;top:1694px;width:480px;font-size:31px;line-height:38px}
.photo{left:681px;top:1715px;width:393px;height:376px;background:linear-gradient(135deg,#c8ccd2,#8b8f96 50%,#5a5c62)}

/* industries */
.industries{left:0;top:2206px;width:1200px;height:797px;background:var(--pale)}
.ind{width:313px;text-align:center}
.ind svg{display:block;margin:0 auto}
.ind h4{font-size:18px;font-weight:500;color:var(--ink);margin-top:20px}
.ind p{font-size:14px;line-height:25px;color:var(--muted);margin-top:12px}
.vline{width:1px;background:var(--line)}
.hline{height:1px;background:var(--line)}

/* process */
.step{width:265px;height:194px;background:var(--pale);border-bottom:3px solid var(--blue);padding:30px 20px}
.step h5{font-size:16px;font-weight:500;color:var(--ink);line-height:24px}
.step p{font-size:14px;line-height:25px;color:var(--muted);margin-top:24px;text-align:justify}
.stage{right:115px;text-align:right;font-size:19px;line-height:27px;text-transform:uppercase}
.stage.on{color:var(--ink)}
.stage.off{color:#666}

/* footer */
.footer{left:0;top:3650px;width:1200px;height:360px;background:linear-gradient(160deg,#2a86d6,#1b70bf 60%,#1a66b0)}
.f-h{font-size:17px;font-weight:500;color:var(--white)}
.f-link{font-size:15px;color:var(--white)}
.f-link::before{content:"»";margin-right:8px}
.subscribe{left:821px;top:3772px;width:265px;height:36px;background:var(--white);border-radius:18px}
.subscribe span{position:absolute;left:18px;top:9px;font-size:14px;color:var(--muted)}
.subscribe b{position:absolute;right:0;top:0;width:94px;height:36px;border-radius:18px;background:#111;color:var(--white);font-size:14px;font-weight:500;display:flex;align-items:center;justify-content:center}
.social{width:36px;height:36px;border-radius:50%;background:var(--white);color:var(--blue);font-size:12px;font-weight:500;display:flex;align-items:center;justify-content:center;top:3826px}
.f-rule{left:110px;top:3937px;width:979px;height:1px;background:rgba(255,255,255,.5)}
.copy{left:0;top:3960px;width:1200px;font-size:15px;color:var(--white)}
</style>
</head>
<body>

<!-- header -->
<div class="abs topbar"></div>
<div class="abs header"></div>
<div class="abs brand"><div class="brand-mark"></div><div class="brand-name">MARWICK PARTNERS</div></div>
<div class="abs nav-mark"></div>
<div class="abs nav active" style="left:491px">Home</div>
<div class="abs nav" style="left:567px">About Us</div>
<div class="abs nav" style="left:665px">Services</div>
<div class="abs nav" style="left:759px">Industries</div>
<div class="abs nav" style="left:862px">Our Success</div>
<div class="abs nav" style="left:983px">Contact</div>
<svg class="abs" style="left:1071px;top:44px" width="14" height="14" viewBox="0 0 14 14"><circle cx="6" cy="6" r="4.5" fill="none" stroke="#1d1d1d" stroke-width="2"/><line x1="9.5" y1="9.5" x2="13" y2="13" stroke="#1d1d1d" stroke-width="2"/></svg>

<!-- hero -->
<div class="abs hero" role="img" aria-label="Skyline view from a high office window with a team of silhouetted professionals celebrating success"></div>
<div class="abs hero-band"></div>
<div class="abs hero-title serif center">Does Your Business Have<br>an Exit Plan?</div>
<div class="abs hero-sub center">Let us help you with a completely impartial, no obligation assessment</div>
<div class="abs btn-frame" style="left:503px;top:453px;width:193px;height:70px"><div class="btn" style="font-size:18px">CONTACT US
<svg width="16" height="16" viewBox="0 0 16 16"><circle cx="8" cy="8" r="7.5" fill="#fff"/><path d="M6 4l4 4-4 4" fill="none" stroke="#1f7fd1" stroke-width="2"/></svg></div></div>
<div class="abs arrow" style="left:33px;top:352px"><svg width="36" height="36" viewBox="0 0 36 36"><path d="M21 11l-7 7 7 7" fill="none" stroke="#fff" stroke-width="2"/></svg></div>
<div class="abs arrow" style="left:1127px;top:352px"><svg width="36" height="36" viewBox="0 0 36 36"><path d="M15 11l7 7-7 7" fill="none" stroke="#fff" stroke-width="2"/></svg></div>

<!-- about -->
<div class="abs eyebrow center">About Us</div>
<div class="abs h2 serif center" style="top:780px">Marwick Partners</div>
<p class="abs body-p center" style="left:135px;top:845px;width:930px">Lorem ipsum dolor sit amet, consectetur adipiscing elit, sed do eiusmod tempor incididunt ut labore et dolore magna aliqua. Ut enim ad minim veniam, quis nostrud exercitation ullamco laboris nisi ut aliquip ex ea commodo consequat. Duis aute irure dolor in reprehenderit in voluptate velit esse cillum dolore eu fugiat nulla pariatur. Excepteur sint occaecat cupidatat non proident, sunt in culpa qui officia deserunt mollit anim id Sed ut perspiciatis unde omnis iste natus error sit voluptatem accusantium</p>
<div class="abs btn-frame" style="left:517px;top:989px;width:166px;height:63px"><div class="btn">LEARN MORE
<svg width="14" height="14" viewBox="0 0 16 16"><circle cx="8" cy="8" r="7.5" fill="#fff"/><path d="M6 4l4 4-4 4" fill="none" stroke="#1f7fd1" stroke-width="2"/></svg></div></div>

<!-- services -->
<div class="abs services" role="img" aria-label="Soft blue-toned photo of business people in a meeting"></div>
<div class="abs h2 serif center" style="top:1212px">Our Services</div>

<div class="abs card" style="left:110px"><div class="card-icon"><svg width="40" height="40" viewBox="0 0 40 40" fill="none" stroke="#fff" stroke-width="2"><rect x="4" y="6" width="20" height="30"/><rect x="24" y="14" width="12" height="22"/><path d="M9 12h10M9 18h10M9 24h10M28 20h4M28 26h4"/></svg></div><h3>Accountant</h3><p>Sed ut perspiciatis unde omnis iste natus error sit voluptatem accusantium doloremque</p></div>
<div class="abs card" style="left:362px"><div class="card-icon"><svg width="40" height="40" viewBox="0 0 40 40" fill="none" stroke="#fff" stroke-width="2"><circle cx="14" cy="10" r="5"/><path d="M5 36V24a9 9 0 0118 0v12"/><path d="M26 22l6-8 6 8M29 22v12h6V22"/></svg></div><h3>Investment Banker</h3><p>Sed ut perspiciatis unde omnis iste natus error sit voluptatem accusantium doloremque</p></div>
<div class="abs card" style="left:616px"><div class="card-icon"><svg width="40" height="40" viewBox="0 0 40 40" fill="none" stroke="#fff" stroke-width="2"><path d="M4 20L18 7l14 13M8 17v17h16"/><rect x="14" y="24" width="7" height="10"/><circle cx="31" cy="30" r="5"/></svg></div><h3>Trust &amp; Estate Attorney</h3><p>Sed ut perspiciatis unde omnis iste natus error sit voluptatem accusantium doloremque</p></div>
<div class="abs card" style="left:868px"><div class="card-icon"><svg width="40" height="40" viewBox="0 0 40 40" fill="none" stroke="#fff" stroke-width="2"><path d="M4 36V8h6v14l8-6v6l8-6v6l8-6v20z"/><path d="M10 30h3M17 30h3M24 30h3"/></svg></div><h3>Corporate Attorney</h3><p>Sed ut perspiciatis unde omnis iste natus error sit voluptatem accusantium doloremque</p></div>

<div class="abs side-arrow" style="left:33px"><svg width="38" height="38" viewBox="0 0 38 38"><path d="M22 12l-7 7 7 7" fill="none" stroke="#1f7fd1" stroke-width="2"/></svg></div>
<div class="abs side-arrow" style="left:1127px"><svg width="38" height="38" viewBox="0 0 38 38"><path d="M16 12l7 7-7 7" fill="none" stroke="#1f7fd1" stroke-width="2"/></svg></div>

<!-- feature -->
<h2 class="abs feature-h serif" style="font-weight:700">We arrive before a problem does, with an end-to-end business solution.</h2>
<p class="abs body-p" style="left:110px;top:1836px;width:490px;text-align:justify">At vero eos et accusamus et iusto odio dignissimos ducimus blanditiis praesentium voluptatum deleniti atque corrupti quos dolores et quas molestias excepturi sint occaecati cupiditate non provident, similique sunt in culpa qui officia deserunt mollitia animi, id est laborum dolorum fuga. Et harum quidem rerum facilis est et expedita distinctio. Nam nihil impedit quo minus id quod maxime placeat facere possimus.</p>
<div class="abs btn-frame" style="left:108px;top:2042px;width:167px;height:63px"><div class="btn">LEARN MORE
<svg width="14" height="14" viewBox="0 0 16 16"><circle cx="8" cy="8" r="7.5" fill="#fff"/><path d="M6 4l4 4-4 4" fill="none" stroke="#1f7fd1" stroke-width="2"/></svg></div></div>
<div class="abs photo" role="img" aria-label="Team of colleagues reviewing documents together at a desk"></div>

<!-- industries -->
<div class="abs industries"></div>
<div class="abs h2 serif center" style="top:2276px">Industries</div>
<div class="abs vline" style="left:423px;top:2368px;height:441px"></div>
<div class="abs vline" style="left:772px;top:2368px;height:441px"></div>
<div class="abs hline" style="left:110px;top:2602px;width:979px"></div>

<div class="abs ind" style="left:83px;top:2365px"><svg width="56" height="60" viewBox="0 0 56 60" fill="none" stroke="#1f7fd1" stroke-width="2"><path d="M22 4h10v10h10v10H32v10H22V24H12V14h10z"/><path d="M4 46h14l10 4 18-8c4-2 6 2 3 4L30 56H4"/></svg><h4>Healthcare</h4><p>Lorem ipsum dolor sit consectetur adipiscing eiusmod tempor incididunt ut labore et dolore magna aliqua.</p></div>
<div class="abs ind" style="left:437px;top:2365px"><svg width="56" height="64" viewBox="0 0 56 64" fill="none" stroke="#1f7fd1" stroke-width="2"><path d="M21 22h14v34a7 7 0 01-14 0z"/><path d="M21 40h14M28 22V8M28 14c-6-2-8-8-6-12 5 1 7 6 6 12zM28 12c5-3 9-2 11 1-3 4-8 4-11-1"/></svg><h4>Life Sciences</h4><p>Lorem ipsum dolor sit consectetur adipiscing eiusmod tempor incididunt ut labore et dolore magna aliqua.</p></div>
<div class="abs ind" style="left:790px;top:2365px"><svg width="64" height="64" viewBox="0 0 64 64" fill="none" stroke="#1f7fd1" stroke-width="2"><path d="M4 24a28 20 0 0156 0z"/><path d="M32 4v20"/><circle cx="24" cy="34" r="5"/><circle cx="40" cy="34" r="5"/><path d="M14 60V50a10 8 0 0120 0v10M30 60V50a10 8 0 0120 0v10"/></svg><h4>Insurance</h4><p>Lorem ipsum dolor sit consectetur adipiscing eiusmod tempor incididunt ut labore et dolore magna aliqua.</p></div>

<div class="abs ind" style="left:83px;top:2630px"><svg width="84" height="48" viewBox="0 0 84 48" fill="none" stroke="#1f7fd1" stroke-width="2"><path d="M4 36V6h62l14 18v12z"/><path d="M4 16h66M16 6v10M30 6v10M44 6v10M58 6v10"/><circle cx="20" cy="38" r="6" fill="#eef6fd"/><circle cx="62" cy="38" r="6" fill="#eef6fd"/></svg><h4>Transportation &amp; Hospitality</h4><p>Lorem ipsum dolor sit consectetur adipiscing eiusmod tempor incididunt ut labore et dolore magna aliqua.</p></div>
<div class="abs ind" style="left:437px;top:2630px"><svg width="50" height="50" viewBox="0 0 50 50" fill="none" stroke="#1f7fd1" stroke-width="2"><ellipse cx="25" cy="25" rx="22" ry="8"/><ellipse cx="25" cy="25" rx="22" ry="8" transform="rotate(60 25 25)"/><ellipse cx="25" cy="25" rx="22" ry="8" transform="rotate(120 25 25)"/><circle cx="25" cy="25" r="4" fill="#1f7fd1"/></svg><h4>Energy, Utilities, Oil &amp; Gas</h4><p>Lorem ipsum dolor sit consectetur adipiscing eiusmod tempor incididunt ut labore et dolore magna aliqua.</p></div>
<div class="abs ind" style="left:790px;top:2630px"><svg width="54" height="50" viewBox="0 0 54 50" fill="none" stroke="#1f7fd1" stroke-width="2"><path d="M10 40a22 22 0 0130-30z"/><path d="M25 25l12-12M34 10l6 6"/><path d="M8 48h30M18 40l-4 8M30 40l4 8"/><path d="M44 6a8 8 0 016 6M44 1a14 14 0 0111 11"/></svg><h4>Technology&amp; Telecommunications</h4><p>Lorem ipsum dolor sit consectetur adipiscing eiusmod tempor incididunt ut labore et dolore magna aliqua.</p></div>

<div class="abs btn-frame" style="left:517px;top:2863px;width:166px;height:63px"><div class="btn">VIEW MORE
<svg width="14" height="14" viewBox="0 0 16 16"><circle cx="8" cy="8" r="7.5" fill="#fff"/><path d="M6 4l4 4-4 4" fill="none" stroke="#1f7fd1" stroke-width="2"/></svg></div></div>

<!-- process -->
<div class="abs step" style="left:110px;top:3117px"><h5>Business Review &amp;<br>Assessment</h5><p>Lorem ipsum amet, consectetur adipiscing elit, do eiusmod tempor incididunt ut labore et dolore</p></div>
<div class="abs step" style="left:411px;top:3117px"><h5>Growth and Fix Plan</h5><p style="margin-top:48px">Lorem ipsum amet, consectetur adipiscing elit, do eiusmod tempor incididunt ut labore et dolore</p></div>
<div class="abs step" style="left:110px;top:3349px"><h5>Customer Experience<br>Enhancement</h5><p>Lorem ipsum amet, consectetur adipiscing elit, do eiusmod tempor incididunt ut labore et dolore</p></div>
<div class="abs step" style="left:411px;top:3349px"><h5>Process Reengineering</h5><p style="margin-top:48px">Lorem ipsum amet, consectetur adipiscing elit, do eiusmod tempor incididunt ut labore et dolore</p></div>

<div class="abs stage on" style="top:3190px">Transform and grow<br>your business</div>
<div class="abs" style="left:680px;top:3269px;width:400px;height:2px;background:var(--ink)"></div>
<div class="abs" style="left:1067px;top:3259px;width:18px;height:22px;background:var(--ink)"></div>
<div class="abs stage off" style="top:3320px">Prepare your business<br>for sale</div>
<div class="abs stage off" style="top:3413px">Launch your new<br>business</div>

<!-- footer -->
<div class="abs footer" role="img" aria-label="Blue-tinted aerial city view"></div>
<div class="abs f-h" style="left:110px;top:3722px">Quick Links</div>
<div class="abs f-link" style="left:110px;top:3764px">Home</div>
<div class="abs f-link" style="left:110px;top:3797px">About Us</div>
<div class="abs f-link" style="left:110px;top:3830px">Services</div>
<div class="abs f-link" style="left:110px;top:3862px">Industries</div>
<div class="abs f-link" style="left:110px;top:3895px">Contact Us</div>

<div class="abs f-h" style="left:339px;top:3720px">Contact Us</div>
<svg class="abs" style="left:339px;top:3768px" width="12" height="16" viewBox="0 0 12 16"><path d="M6 0a6 6 0 016 6c0 4-6 10-6 10S0 10 0 6a6 6 0 016-6z" fill="#fff"/><circle cx="6" cy="6" r="2" fill="#1f7fd1"/></svg>
<div class="abs f-link" style="left:358px;top:3764px;font-size:15px;line-height:21px">123, Lorem ipsum dolor amet<br>consectetur adipiscing</div>
<svg class="abs" style="left:339px;top:3822px" width="14" height="14" viewBox="0 0 14 14"><path d="M3 1l3 3-2 2c1 2 2 3 4 4l2-2 3 3-2 2C6 13 1 8 1 3z" fill="#fff"/></svg>
<div class="abs" style="left:358px;top:3818px;font-size:15px;color:#fff">(555) 010-4420</div>
<svg class="abs" style="left:337px;top:3857px" width="16" height="12" viewBox="0 0 16 12"><rect x="1" y="1" width="14" height="10" fill="none" stroke="#fff" stroke-width="1.5"/><path d="M1 1l7 6 7-6" fill="none" stroke="#fff" stroke-width="1.5"/></svg>
<div class="abs" style="left:358px;top:3852px;font-size:15px;color:#fff">info@marwickpartners.example</div>

<div class="abs f-h" style="left:632px;top:3721px">Important</div>
<div class="abs f-link" style="left:632px;top:3766px">Terms of Use</div>
<div class="abs f-link" style="left:632px;top:3799px">Site Map</div>
<div class="abs f-link" style="left:632px;top:3831px">Privacy Policy</div>
<div class="abs f-link" style="left:632px;top:3864px">Disclaimer</div>

<div class="abs f-h" style="left:820px;top:3723px">Newsletter Subscription</div>
<div class="abs subscribe"><span>Enter your email</span><b>SUBMIT</b></div>
<div class="abs social" style="left:822px">FB</div>
<div class="abs social" style="left:869px">TW</div>
<div class="abs social" style="left:916px">LI</div>

<div class="abs f-rule"></div>
<div class="abs copy center">© 2020 Marwick Partners. All Rights Reserved</div>

</body>
</html>
```